Personal loan pre-approval

We are a credit union sending out pre-approvals for personal loans. I am attaching a letter that we sent out during previous pre-approvals. The fine print needs to be included on the postcard from the letter, but the rest is just a guide. The theme I'm thinking of may be Easy, Cold Hard Cash, but I'm not stuck on it. Thanks.

http://www.brightleafprint.com/gallerydetail.aspx?sectionID=143&photoID=104

The cash banner is an example of what I had in mind.

We don't want the actual letter on the postcard, it was meant to be a guide only as to what we are selling. The front page should be explaining that they are pre-approved for a personal loan, say up $10,000, at a rate of 7.99% APR*. It should be mentioned how they are pre-approved, which means no credit check, no proof of income needed. Somewhere, either on the front or the back, needs to be the fine print in a discreet fashion. look at the link I provide for some guidance. Thanks!
Updates

Industry/Entity Type

Union

Requirements
Must have
• Must have fine print on postcard that is on example letter.
Should not have
• Should not have the entire letter on the postcard

```html
<!DOCTYPE html>
<html lang="en">
<head>
<meta charset="utf-8">
<title>Signature Loan Pre-Approval</title>
<link rel="stylesheet" href="https://fonts.googleapis.com/css2?family=Archivo+Black&family=PT+Serif:wght@400;700&family=Gochi+Hand&family=Oswald:wght@600&family=Open+Sans:wght@400&display=swap">
<style>
  :root{
    --navy:#233a86;
    --navy-deep:#1b2c6e;
    --lavender-1:#c9c8e3;
    --lavender-2:#8d8ec2;
    --lavender-3:#6b6da8;
    --yellow:#f4d03f;
    --red:#e0202a;
    --white:#ffffff;
    --ink:#2a2a3a;
    --black:#0a0a0a;
  }
  *{margin:0;padding:0;box-sizing:border-box}
  html,body{width:911px;height:1200px;overflow:hidden;background:var(--white)}
  .card{position:relative;width:911px;height:1200px;background:var(--white);font-family:"PT Serif",serif}
  h1,h2{font-weight:400}

  /* Hero */
  .hero{position:absolute;left:0;top:0;width:911px;height:588px;
    background:linear-gradient(160deg,#e9d9cf 0%,#d8b9a8 30%,#c8a7c9 55%,#a98fc4 75%,#ecdcd2 100%)}
  .hero-photo{position:absolute;inset:0}
  .hero-strip{position:absolute;left:0;top:588px;width:911px;height:18px;background:var(--black)}
  .pre-approved{position:absolute;left:34px;top:76px;font-family:"Archivo Black",sans-serif;font-size:22px;white-space:nowrap;
    color:var(--navy);-webkit-text-stroke:1.5px var(--white);paint-order:stroke fill}
  .amount,.product{position:absolute;left:30px;font-family:"Archivo Black",sans-serif;color:var(--white);white-space:nowrap;
    -webkit-text-stroke:3px var(--navy);paint-order:stroke fill;line-height:1;font-size:68px}
  .amount{top:126px}
  .product{top:204px;letter-spacing:-1px}
  .terms{position:absolute;left:288px;top:308px;font-family:"Open Sans",sans-serif;font-size:18px;color:var(--ink);line-height:1.3}

  .brand{display:flex;align-items:center;gap:8px;color:var(--navy);font-family:"PT Serif",serif}
  .brand-mark{width:30px;height:30px;background:var(--navy);flex:none}
  .brand-name{font-size:14px;line-height:1.15;width:130px}
  .hero .brand{position:absolute;left:726px;top:50px}

  .rate-band{position:absolute;left:0;top:504px;width:600px;height:84px}
  .rate-label{position:absolute;left:36px;top:540px;font-size:20px;color:var(--white);white-space:nowrap}
  .rate-value{position:absolute;left:186px;top:504px;font-size:62px;color:var(--white);letter-spacing:2px;white-space:nowrap;
    text-shadow:1px 2px 0 rgba(0,0,0,.45)}

  /* Holiday panel */
  .holiday{position:absolute;left:0;top:612px;width:762px;height:144px;
    background:linear-gradient(90deg,var(--lavender-1) 0%,#b4b3d8 45%,var(--lavender-3) 100%)}
  .holiday .brand{position:absolute;left:26px;top:44px}
  .holiday .brand-mark{width:44px;height:44px}
  .holiday .brand-name{font-size:19px;width:210px}
  .holiday-line{position:absolute;left:300px;top:48px;font-family:"Gochi Hand",cursive;font-size:33px;color:var(--red);white-space:nowrap;
    -webkit-text-stroke:3px var(--white);paint-order:stroke fill}

  /* Headline band */
  .headline-band{position:absolute;left:0;top:758px;width:911px;height:108px;background:var(--navy)}
  .headline-main{position:absolute;left:26px;top:16px;font-size:40px;color:var(--yellow);white-space:nowrap}
  .headline-sub{position:absolute;left:368px;top:48px;font-size:36px;color:var(--red);white-space:nowrap}

  /* Offer panel */
  .offer{position:absolute;left:0;top:870px;width:604px;height:330px;
    background:linear-gradient(90deg,var(--lavender-2) 0%,#a9a9d2 55%,var(--lavender-1) 100%)}
  .offer-head{position:absolute;left:0;top:26px;width:410px;text-align:center;font-family:"Archivo Black",sans-serif;
    font-size:20px;line-height:1.45;color:var(--white);-webkit-text-stroke:3px var(--navy-deep);paint-order:stroke fill;white-space:nowrap}
  .offer-head .approved{color:var(--red);-webkit-text-stroke:3px var(--white)}
  .offer-body{position:absolute;left:24px;top:142px;width:400px;font-size:11.4px;line-height:1.3;color:var(--white)}
  .fine-print{position:absolute;left:24px;width:400px;font-size:8.2px;line-height:1.35;color:var(--white)}
  .fine-print.terms-note{top:214px}
  .fine-print.prescreen{top:254px}

  .burst{position:absolute;left:390px;top:858px;width:204px;height:204px}
  .burst-text{position:absolute;left:390px;top:906px;width:204px;text-align:center;font-family:"Oswald",sans-serif;
    font-size:20px;line-height:1.3;text-transform:uppercase}
  .burst-text .lead{color:var(--yellow)}
  .burst-text .date{color:var(--white)}
</style>
</head>
<body>
<div class="card">

  <section class="hero">
    <div class="hero-photo" role="img" aria-label="Close-up photo of hands signing a loan document with a fountain pen beside a stack of cash"></div>

    <div class="brand">
      <span class="brand-mark"></span>
      <span class="brand-name">Harbor Valley Teachers Credit Union</span>
    </div>

    <p class="pre-approved">You have been pre-approved for up to:</p>
    <h1 class="amount">$10,000</h1>
    <h1 class="product">Signature Loan</h1>
    <p class="terms">including existing loan balances*<br>Up to 60 month term</p>

    <svg class="rate-band" viewBox="0 0 600 84" aria-hidden="true">
      <polygon points="0,0 540,0 600,84 0,84" fill="var(--navy)"/>
    </svg>
    <p class="rate-label">Rate as low as</p>
    <p class="rate-value">7.99% APR*</p>
  </section>
  <div class="hero-strip"></div>

  <section class="holiday">
    <div class="brand">
      <span class="brand-mark"></span>
      <span class="brand-name">Harbor Valley Teachers Credit Union</span>
    </div>
    <p class="holiday-line">imagine this holiday season!</p>
  </section>

  <section class="headline-band">
    <h2 class="headline-main">Personal Loans...</h2>
    <h2 class="headline-sub">at Unbeatable Rates</h2>
  </section>

  <section class="offer">
    <p class="offer-head">NO CREDIT CHECK,<br>NO PROOF OF INCOME.<br><span class="approved">YOU'RE ALREADY APPROVED!</span></p>
    <p class="offer-body">You are able to use these funds for whatever you like! The possibilities are limitless; Holiday shopping, school supplies, an exotic vacation, new computer, padding your savings or consolidating your debts. This is a fixed rate loan, so this great low rate won't change over the life of the loan.</p>
    <p class="fine-print terms-note">*Maximum unsecured amount is $25,000 including existing loan balances. Existing loan will be paid in full and rolled into new loan at new rate. Minimum advance must be $250. Offer is subject to completion of loan documents and Credit Union membership. See Credit Union for details. Certain restrictions may apply.</p>
    <p class="fine-print prescreen">PRESCREEN &amp; OPT-OUT NOTICE: This "prescreened" offer of credit is based on information in your credit report indicating that you have met certain criteria. This offer is not guaranteed if you do not meet our criteria. You can choose to stop receiving "prescreened" offers of credit from this and other companies by calling toll-free 1-800-555-0142; or write: Credit Bureau Opt-Out Center, 400 Ledger Lane, Fairview, TX 75099.</p>
  </section>

  <svg class="burst" viewBox="-100 -100 200 200" aria-hidden="true">
    <polygon fill="var(--navy-deep)" points="0,-98 13,-83 31,-93 37,-74 57,-79 55,-59 76,-57 65,-39 84,-29 69,-15 83,0 69,15 84,29 65,39 76,57 55,59 57,79 37,74 31,93 13,83 0,98 -13,83 -31,93 -37,74 -57,79 -55,59 -76,57 -65,39 -84,29 -69,15 -83,0 -69,-15 -84,-29 -65,-39 -76,-57 -55,-59 -57,-79 -37,-74 -31,-93 -13,-83"/>
  </svg>
  <p class="burst-text"><span class="lead">Special<br>Pre-Approval<br>Offer Expires</span><br><span class="date">Dec. 31st,<br>2014!</span></p>

</div>
</body>
</html>
```